Investor Slide Deck

Simple idea - take a model investor deck and build out a investor deck for K7V. I will complete the data, I need a template to work from within. I will attach a model investor deck and a blank K7V that I need built out to K7V. Use the K7V Pwrpt to build out the investor deck

```html
<!DOCTYPE html>
<html lang="en">
<head>
<meta charset="utf-8">
<title>K7V Investor Deck 2024</title>
<link href="https://fonts.googleapis.com/css2?family=Nunito:wght@500;600;700;800&family=Source+Sans+3:wght@400;600;700&display=swap" rel="stylesheet">
<style>
:root{
  --ink:#052f3a;
  --orange:#f4511e;
  --blue:#1d6a8a;
  --yellow:#f9bf2d;
  --page:#d7e5ea;
  --text:#2a3a40;
  --white:#ffffff;
  --pink:#fde7df;
  --sky:#e2f3f8;
  --cream:#fef4dc;
  --peer-bg:#eef3f5;
}
*{margin:0;padding:0;box-sizing:border-box}
html,body{width:1017px;height:1200px;overflow:hidden;background:var(--page)}
body{font-family:"Source Sans 3",sans-serif;color:var(--text)}
.stage{position:absolute;left:0;top:0;width:1764px;height:2081px;transform:scale(.5765);transform-origin:0 0}
.slide{position:absolute;width:836px;height:469px;background:var(--white);overflow:hidden;box-shadow:0 1px 3px rgba(0,0,0,.08)}
.col-l{left:27px}.col-r{left:892px}
.row-1{top:26px}.row-2{top:541px}.row-3{top:1055px}.row-4{top:1570px}
.abs{position:absolute}
.tri{position:absolute;display:flex;gap:8px}
.tri span{width:40px;height:3px;border-radius:2px}
.tri span:nth-child(1){background:var(--orange)}
.tri span:nth-child(2){background:var(--blue)}
.tri span:nth-child(3){background:var(--yellow)}
.title{position:absolute;left:31px;top:32px;font-family:"Nunito",sans-serif;font-weight:700;font-size:31px;color:var(--ink);letter-spacing:.3px}
.footer{position:absolute;left:35px;top:437px;font-size:11px;font-weight:600;color:var(--ink)}
.pageno{position:absolute;left:772px;top:430px;width:28px;height:28px;border-radius:50%;background:var(--orange);color:#fff;font-size:11px;font-weight:700;display:flex;align-items:center;justify-content:center}
.mark{position:absolute;left:766px;top:34px;font-family:"Nunito",sans-serif;font-weight:800;font-size:22px;color:var(--orange)}
.mark.light{color:var(--white)}
.tick{width:12px;height:12px;flex:none;margin-top:3px}
.list{list-style:none;font-size:13px;line-height:19.5px}
.list li{display:flex;gap:9px}
.list b{color:var(--ink)}
/* cover + thanks */
.hero{background:var(--ink)}
.hero .photo{position:absolute;inset:0;background:linear-gradient(180deg,#0a3b48 0%,#0c3f4a 45%,#1b4d42 100%)}
.brand{position:absolute;left:0;right:0;text-align:center;color:#fff}
.brand-mark{font-family:"Nunito",sans-serif;font-weight:800;font-size:72px;color:var(--orange);line-height:1}
.brand-name{font-family:"Nunito",sans-serif;font-weight:600;font-size:27px;letter-spacing:.5px}
.hero-head{font-family:"Nunito",sans-serif;font-weight:600;font-size:31px;line-height:39px;letter-spacing:.3px}
.hero-sub{font-size:22px;font-weight:400}
/* target markets */
.map{position:absolute;top:101px;width:353px;height:214px;border-radius:10px;background:radial-gradient(circle at 50% 50%,#3c6a76 0%,#0b3a46 55%,var(--ink) 100%)}
/* problems */
.prob-item{position:absolute;width:380px}
.prob-item h3,.sol-item h3{font-size:14px;font-weight:700;color:var(--ink);margin-bottom:4px}
.prob-item p{font-size:12.5px;line-height:19.5px}
.icon-dot{position:absolute;width:54px;height:54px;border-radius:50%;background:var(--orange);border:3px solid #fff;box-shadow:0 0 0 2px rgba(244,81,30,.25)}
/* competitors */
.sub{position:absolute;left:32px;top:78px;font-size:13px}
.group{position:absolute;top:124px;font-size:17px;font-weight:700;color:var(--ink)}
.peer{position:absolute;height:44px;padding:0 14px;display:flex;align-items:center;background:var(--peer-bg);border-radius:4px;font-family:"Source Sans 3",sans-serif;font-weight:700;font-size:19px;color:var(--ink)}
.hub{position:absolute;left:347px;top:297px;width:139px;height:139px;border-radius:50%;background:var(--ink);color:#fff;text-align:center;padding-top:38px}
.hub .m{font-family:"Nunito",sans-serif;font-weight:800;font-size:28px;color:var(--orange)}
.hub .n{font-size:10.5px;font-weight:700;margin-top:6px}
/* solutions */
.sol-dark{position:absolute;left:416px;top:0;width:420px;height:469px;background:var(--ink)}
.sol-item{position:absolute;width:320px}
.sol-item p{font-size:12.5px;line-height:19.5px}
.num{position:absolute;width:32px;height:32px;border-radius:50%;color:#fff;font-size:12px;font-weight:700;display:flex;align-items:center;justify-content:center}
.sol-dark .sol-item h3{color:#fff}
.sol-dark .sol-item p{color:#e3edf0}
/* financial */
.unit{position:absolute;left:32px;top:76px;font-size:18px;font-weight:700;color:var(--ink)}
.legend{position:absolute;left:585px;font-size:12.5px;display:flex;align-items:center;gap:10px}
.legend i{width:13px;height:13px;display:block}
/* services */
.card{position:absolute;top:101px;width:240px;height:309px;border-radius:8px;overflow:hidden}
.card .shot{height:145px}
.card h3{font-size:14px;font-weight:700;color:var(--ink);margin:12px 0 8px 22px}
.card .list{margin-left:22px;font-size:12.5px;margin-right:14px}
/* thank you */
.contacts{position:absolute;left:32px;right:30px;top:317px;display:flex;justify-content:space-between;color:#fff;font-size:16px;line-height:24px}
.contacts div{display:flex;gap:12px}
.contacts svg{width:13px;height:14px;margin-top:5px;flex:none}
.contacts b{font-weight:600}
</style>
</head>
<body>
<svg width="0" height="0" style="position:absolute" aria-hidden="true">
  <symbol id="tick" viewBox="0 0 12 12"><circle cx="6" cy="6" r="5" fill="none" stroke="currentColor" stroke-width="1.4"/><path d="M3.6 6.1l1.7 1.7 3.2-3.4" fill="none" stroke="currentColor" stroke-width="1.4" stroke-linecap="round" stroke-linejoin="round"/></symbol>
  <symbol id="pin" viewBox="0 0 12 14"><path d="M6 0a5 5 0 0 0-5 5c0 3.6 5 9 5 9s5-5.4 5-9a5 5 0 0 0-5-5zm0 7a2 2 0 1 1 0-4 2 2 0 0 1 0 4z" fill="currentColor"/></symbol>
  <symbol id="phone" viewBox="0 0 14 14"><path d="M3 1l2.2 2.8-1.3 1.6a8 8 0 0 0 4.7 4.7l1.6-1.3L13 11l-1.4 2.2C6 13 1 8 .8 2.4z" fill="currentColor"/></symbol>
</svg>

<main class="stage">

  <!-- Cover -->
  <section class="slide hero col-l row-1">
    <div class="photo" role="img" aria-label="Solar panel field under a dark teal overlay"></div>
    <div class="brand" style="top:88px"><div class="brand-mark">K7V</div></div>
    <div class="brand brand-name" style="top:195px">KESTREL 7 VENTURES</div>
    <div class="tri" style="left:354px;top:254px"><span></span><span></span><span></span></div>
    <div class="brand hero-head" style="top:264px">SUSTAINABLE FUTURE FOR<br>CURRENT AND UPCOMING GENERATIONS</div>
    <div class="brand hero-sub" style="top:352px">Investor Deck, 2024</div>
  </section>

  <!-- Target markets -->
  <section class="slide col-r row-1">
    <div class="tri" style="left:31px;top:22px"><span></span><span></span><span></span></div>
    <h2 class="title">TARGET MARKETS</h2>
    <div class="map" style="left:32px" role="img" aria-label="Map of India with short and medium term states highlighted"></div>
    <div class="map" style="left:447px" role="img" aria-label="World map with Middle East and Africa highlighted"></div>
    <ul class="list abs" style="left:32px;top:341px;color:var(--orange)">
      <li><svg class="tick"><use href="#tick"/></svg><span style="color:var(--text)"><b>Short Term</b> – Location, Maharashtra, MP, Maharashtra</span></li>
      <li><svg class="tick"><use href="#tick"/></svg><span style="color:var(--text)"><b>Medium Term</b> – All Indian States with Solar Power Demand</span></li>
      <li><svg class="tick"><use href="#tick"/></svg><span style="color:var(--text)">Setting up of Certification process for Export Markets</span></li>
    </ul>
    <ul class="list abs" style="left:447px;top:341px;color:var(--yellow)">
      <li><svg class="tick"><use href="#tick"/></svg><span style="color:var(--text)"><b>Long Term –</b> India.</span></li>
      <li><svg class="tick"><use href="#tick"/></svg><span style="color:var(--text)"><b>Export Markets -</b> Middle East and African Continent</span></li>
    </ul>
    <div class="footer">Private &amp; Confidential | 2024</div>
    <div class="pageno">05</div>
  </section>

  <!-- Problems -->
  <section class="slide col-l row-2">
    <svg class="abs" style="left:0;top:0" width="836" height="469" aria-hidden="true">
      <defs>
        <clipPath id="problem-panel"><path d="M0 0H292C420 120 390 360 185 469H0Z"/></clipPath>
        <linearGradient id="roof" x1="0" y1="0" x2="0" y2="1"><stop offset="0" stop-color="#5f88b4"/><stop offset="1" stop-color="#1f3f6b"/></linearGradient>
      </defs>
      <path d="M296 0C436 118 406 366 190 469H205C426 362 452 116 320 0Z" fill="var(--yellow)"/>
      <g clip-path="url(#problem-panel)">
        <rect width="836" height="469" fill="var(--ink)"/>
        <rect y="175" width="836" height="294" fill="url(#roof)" role="img" aria-label="Technician with a laptop inspecting rooftop solar panels"/>
      </g>
    </svg>
    <div class="tri" style="left:32px;top:22px"><span></span><span></span><span></span></div>
    <h2 class="title" style="color:#fff">PROBLEMS</h2>
    <p class="abs" style="left:33px;top:74px;width:290px;color:#fff;font-size:14.5px;line-height:22.5px">Every year, the rise in prices of electricity is burning a hole in the pocket of consumers. <b>Solar Power</b> is a reliable solution, but the industry is facing its own set of challenges.</p>
    <div class="footer" style="color:#fff">Private &amp; Confidential | 2024</div>
    <div class="mark">K7V</div>

    <span class="icon-dot" style="left:355px;top:44px"></span>
    <div class="prob-item" style="left:427px;top:46px"><h3>Poor Quality Components</h3><p>The use of low-quality solar panels and components in solar plant construction is impacting their efficiency and lifespan.</p></div>
    <span class="icon-dot" style="left:368px;top:125px"></span>
    <div class="prob-item" style="left:440px;top:127px"><h3>Poor Installation</h3><p>Solar plant installations demand precision; poor installation can lead to downtime, damage, and efficiency loss.</p></div>
    <span class="icon-dot" style="left:354px;top:204px"></span>
    <div class="prob-item" style="left:427px;top:205px"><h3>Lack of Awareness</h3><p>Limited awareness of government subsidies and inadequate financing options for high-cost solar plant purchases can lead to missed product benefits</p></div>
    <span class="icon-dot" style="left:320px;top:303px"></span>
    <div class="prob-item" style="left:392px;top:304px"><h3>Unreliable Customer and Warranty Support</h3><p>Challenges in reaching timely support and clarifying warranty terms can result in customer frustration and self-reliance for issue resolution.</p></div>
    <span class="icon-dot" style="left:264px;top:385px"></span>
    <div class="prob-item" style="left:335px;top:386px;width:410px"><h3>Lack of Transparency in Pricing and Performance</h3><p>Customers might encounter unexpected hidden costs during installation and lower energy generation than initially agreed upon.</p></div>
    <div class="pageno">02</div>
  </section>

  <!-- Competitive analysis -->
  <section class="slide col-r row-2">
    <div class="tri" style="left:31px;top:22px"><span></span><span></span><span></span></div>
    <h2 class="title">COMPETITIVE ANALYSIS</h2>
    <div class="mark">K7V</div>
    <p class="sub">Company Name Energy wants to Manufacture Solar Panels while also taking up EPC Projects for Solar Plants.</p>
    <div class="group" style="left:34px">EPC Providers</div>
    <div class="group" style="left:452px">Solar Panel Manufacturers</div>
    <div class="peer" style="left:32px;top:177px">Nordlys Power</div>
    <div class="peer" style="left:219px;top:192px">Ampora Solar</div>
    <div class="peer" style="left:30px;top:307px">Sunquad</div>
    <div class="peer" style="left:180px;top:310px">Kovaris</div>
    <div class="peer" style="left:454px;top:165px">Waveline</div>
    <div class="peer" style="left:636px;top:165px">Jarrow</div>
    <div class="peer" style="left:458px;top:237px">Renvio</div>
    <div class="peer" style="left:652px;top:221px">Adrion Solar</div>
    <div class="peer" style="left:607px;top:322px">Vikta Solar</div>
    <div class="hub"><div class="m">K7V</div><div class="n">KESTREL 7 VENTURES</div></div>
    <div class="footer">Private &amp; Confidential | 2024</div>
    <div class="pageno">06</div>
  </section>

  <!-- Solutions -->
  <section class="slide col-l row-3">
    <div class="sol-dark"></div>
    <div class="tri" style="left:32px;top:22px"><span></span><span></span><span></span></div>
    <h2 class="title">SOLUTIONS</h2>
    <div class="mark light">K7V</div>
    <span class="num" style="left:33px;top:82px;background:var(--orange)">1</span>
    <div class="sol-item" style="left:80px;top:88px"><h3>Quality Components</h3><p>With a portfolio of 2500+ solar power plants, we excel in selecting technically compatible, premium components to guarantee long-term results, planning an automated facility for high-quality solar panels.</p></div>
    <span class="num" style="left:33px;top:191px;background:var(--blue)">2</span>
    <div class="sol-item" style="left:80px;top:197px"><h3>Awareness About Subsidies And Financing</h3><p>Company Name Energy educates residential consumers about Central Government subsidies and collaborates with banks and NBFCs to facilitate solar financing for various client segments.</p></div>
    <span class="num" style="left:33px;top:304px;background:var(--yellow)">3</span>
    <div class="sol-item" style="left:80px;top:310px"><h3>Dedicated Customer And Warranty Support</h3><p>Company Name Energy's dedicated team offers comprehensive after-sales support, facilitating swift warranty-covered service at local offices for our Panels and Inverters, eliminating brand-related delays.</p></div>
    <div class="sol-dark" style="background:none">
      <span class="num" style="left:17px;top:82px;background:var(--orange)">1</span>
      <div class="sol-item" style="left:63px;top:88px"><h3>Efficient Installation</h3><p>Our proficient design and site engineers create solar plants to precise technicalspecs, ensuring low-maintenance installations with a flawless track record of zero system failures.</p></div>
      <span class="num" style="left:17px;top:191px;background:var(--blue)">2</span>
      <div class="sol-item" style="left:63px;top:197px;width:325px"><h3>Transparent Pricing &amp; Performance</h3><p>We ensure transparent pricing and performance commitments in our projects. Our designs are created with the shadow analysis of solar panels for optimum result. We also provide the projected power generation and payback report of solar plant using software.</p></div>
    </div>
    <div class="footer">Private &amp; Confidential | 2024</div>
    <div class="pageno">03</div>
  </section>

  <!-- Financial overview -->
  <section class="slide col-r row-3">
    <div class="tri" style="left:31px;top:22px"><span></span><span></span><span></span></div>
    <h2 class="title">FINANCIAL OVERVIEW</h2>
    <div class="mark">K7V</div>
    <div class="unit">in ₹Cr</div>
    <svg class="abs" style="left:0;top:0" width="836" height="469" role="img" aria-label="Revenue and EBITDA bar chart over five years" font-family="Source Sans 3, sans-serif" font-weight="700" font-size="13">
      <rect x="322" y="120" width="191" height="276" fill="#fdf6e7"/>
      <line x1="32" y1="396" x2="513" y2="396" stroke="#c8c8c8"/>
      <g fill="var(--blue)">
        <rect x="57" y="372" width="22" height="24"/>
        <rect x="155" y="285" width="22" height="111"/>
        <rect x="251" y="270" width="22" height="126"/>
        <rect x="348" y="160" width="22" height="236"/>
        <rect x="445" y="156" width="22" height="240"/>
      </g>
      <g fill="var(--yellow)">
        <rect x="86" y="394" width="22" height="2"/>
        <rect x="184" y="382" width="22" height="14"/>
        <rect x="281" y="380" width="22" height="16"/>
        <rect x="378" y="358" width="22" height="38"/>
        <rect x="475" y="357" width="22" height="39"/>
      </g>
      <g fill="var(--blue)" text-anchor="middle">
        <text x="65" y="357">₹205</text>
        <text x="162" y="273">₹972</text>
        <text x="265" y="258">₹1,109</text>
        <text x="363" y="151">₹2,088</text>
        <text x="459" y="146">₹2,130</text>
      </g>
      <g fill="var(--yellow)" text-anchor="middle">
        <text x="100" y="384">₹14</text>
        <text x="208" y="362">₹112.5</text>
        <text x="297" y="368">₹141</text>
        <text x="395" y="344">₹315</text>
        <text x="492" y="344">₹335</text>
      </g>
      <path d="M570 164C556 156 538 156 525 160l6-5M525 160l6 5" fill="none" stroke="#666" stroke-width="1.2"/>
    </svg>
    <p class="abs" style="left:581px;top:134px;width:160px;font-size:12.5px;line-height:19.5px">We plan to double our capacity in the 4th year of Operations</p>
    <div class="legend" style="top:209px"><i style="background:var(--yellow)"></i>EBITDA</div>
    <div class="legend" style="top:235px"><i style="background:var(--blue)"></i>Revenue</div>
    <div class="footer">Private &amp; Confidential | 2024</div>
    <div class="pageno">07</div>
  </section>

  <!-- Services -->
  <section class="slide col-l row-4">
    <div class="tri" style="left:32px;top:22px"><span></span><span></span><span></span></div>
    <h2 class="title">OUR SERVICES</h2>
    <article class="card" style="left:32px;background:var(--pink)">
      <div class="shot" role="img" aria-label="House roof covered with solar panels" style="background:linear-gradient(160deg,#6f8fbf,#b0573e 70%,#e8e3dc)"></div>
      <h3>Solar Power for Homes</h3>
      <ul class="list" style="color:var(--orange)">
        <li><svg class="tick"><use href="#tick"/></svg><span style="color:var(--text)">Electricity Bill to go to Zero</span></li>
        <li><svg class="tick"><use href="#tick"/></svg><span style="color:var(--text)">Low Maintenance Cost</span></li>
        <li><svg class="tick"><use href="#tick"/></svg><span style="color:var(--text)">Assured Warranty upto 25 Years</span></li>
        <li><svg class="tick"><use href="#tick"/></svg><span style="color:var(--text)">Government Subsidies</span></li>
      </ul>
    </article>
    <article class="card" style="left:296px;background:var(--sky)">
      <div class="shot" role="img" aria-label="Commercial rooftop with rows of solar panels" style="background:linear-gradient(160deg,#cfd8e0,#3a5785 55%,#26406a)"></div>
      <h3>Solar Power for Business</h3>
      <ul class="list" style="color:var(--blue)">
        <li><svg class="tick"><use href="#tick"/></svg><span style="color:var(--text)">Clean Energy</span></li>
        <li><svg class="tick"><use href="#tick"/></svg><span style="color:var(--text)">Tax Benefits</span></li>
        <li><svg class="tick"><use href="#tick"/></svg><span style="color:var(--text)">Grid Tied Systems</span></li>
        <li><svg class="tick"><use href="#tick"/></svg><span style="color:var(--text)">Finance Support</span></li>
      </ul>
    </article>
    <article class="card" style="left:560px;background:var(--cream)">
      <div class="shot" role="img" aria-label="Utility scale solar farm on green grass" style="background:linear-gradient(180deg,#e9eef3,#3e5f95 50%,#5f8a3c 100%)"></div>
      <h3>Utility Scale Solar Power Plant</h3>
      <ul class="list" style="color:var(--yellow)">
        <li><svg class="tick"><use href="#tick"/></svg><span style="color:var(--text)">Generate and Sell electricity to the government and industrial plants</span></li>
        <li><svg class="tick"><use href="#tick"/></svg><span style="color:var(--text)">Long term stable prices for generated electricity from solar power plant</span></li>
      </ul>
    </article>
    <div class="footer">Private &amp; Confidential | 2024</div>
    <div class="pageno">04</div>
  </section>

  <!-- Thank you -->
  <section class="slide hero col-r row-4">
    <div class="photo" role="img" aria-label="Solar panel field under a dark teal overlay"></div>
    <div class="brand" style="top:92px"><div class="brand-mark">K7V</div></div>
    <div class="brand brand-name" style="top:196px">KESTREL 7 VENTURES</div>
    <div class="tri" style="left:354px;top:247px"><span></span><span></span><span></span></div>
    <div class="brand hero-head" style="top:262px">THANK YOU</div>
    <div class="contacts">
      <div><svg><use href="#pin"/></svg><span><b>Kestrel7Ventures,</b><br>Address comes here</span></div>
      <div><svg><use href="#phone"/></svg><span><b>Call Us</b><br>+1 555-010-0100</span></div>
      <div><svg><use href="#pin"/></svg><span><b>Website</b><br>www.kestrel7v.com</span></div>
      <div><svg><use href="#phone"/></svg><span><b>Email</b><br>info@kestrel7v.com</span></div>
    </div>
  </section>

</main>
</body>
</html>
```